The (Private) News Sharing Report

This is a professional and academic report of 35 pages for journalists and teachers. The topic of the report is News Sharing: journalism, social networks and technology. Attached there is an example of the kind of design we are looking for: visual, fresh and modern.

Target Market(s)

Journalists, Journalism Students, Communication Researchers,

Industry/Entity Type

Media

Font styles to use
Sans Serif

Colors
3276b5
33a6d7
886aae
b868aa

Requirements
Must have
• Copyleft images, visual style
Nice to have
• There is an example attached.

```html
<!DOCTYPE html>
<html lang="en">
<head>
<meta charset="utf-8">
<title>The (Private) News Sharing Report — Research Questions</title>
<link href="https://fonts.googleapis.com/css2?family=Montserrat:ital,wght@0,200;0,300;0,400;0,500;0,600;0,700;1,400&display=swap" rel="stylesheet">
<style>
  :root {
    --backdrop: #adadad;
    --paper: #f5f5f5;
    --ink: #1d1d1f;
    --ink-soft: #3a3a3c;
    --rule: #b9b9b9;
    --accent: #a85ba0;
    --accent-light: #b868aa;
    --accent-violet: #886aae;
  }
  * { margin: 0; padding: 0; box-sizing: border-box; }
  html, body { width: 1200px; height: 900px; overflow: hidden; }
  body {
    background: var(--backdrop);
    font-family: "Montserrat", Arial, sans-serif;
    color: var(--ink);
    position: relative;
  }
  .spread {
    position: absolute; left: 20px; top: 60px;
    width: 1160px; height: 779px;
  }
  .page { position: absolute; top: 0; height: 779px; background: var(--paper); }
  .page--left { left: 0; width: 575px; }
  .page--right { left: 575px; width: 585px; border-left: 1px solid #e2e2e2; }
  .abs { position: absolute; }

  .network-art {
    left: 0; top: 0; width: 170px; height: 185px;
    background: radial-gradient(circle at 10% 5%, rgba(136,106,174,.35), rgba(136,106,174,.08) 55%, rgba(245,245,245,0) 75%);
  }
  .section-title {
    left: 66px; top: 82px;
    font-size: 34px; font-weight: 700; color: var(--accent); letter-spacing: -0.3px;
  }
  .section-intro { left: 66px; top: 126px; font-size: 16px; font-weight: 400; color: var(--ink); }

  .question { position: absolute; top: 175px; width: 90px; }
  .question__num { font-size: 96px; font-weight: 200; line-height: 100px; color: var(--ink); }
  .question__text { margin-top: 8px; font-size: 11.5px; line-height: 13.4px; font-weight: 300; color: var(--ink-soft); }

  .divider { left: 65px; top: 391px; width: 1045px; height: 1px; background: var(--rule); }

  .chapter-title { left: 66px; top: 448px; font-size: 19px; font-weight: 400; }
  .chapter-body { left: 66px; top: 476px; width: 212px; font-size: 8.6px; line-height: 12px; color: var(--ink); }
  .chapter-body strong { font-weight: 700; }
  .chapter-body p + p { text-indent: 10px; }

  .quadrant-label { font-size: 17px; font-weight: 300; color: var(--accent-light); }
  .quadrant-label b { font-weight: 700; color: var(--ink); }
  .headline-word { font-size: 55px; font-weight: 200; color: var(--accent-light); line-height: 1; letter-spacing: 1px; }
  .map-note { font-size: 10.5px; font-weight: 600; color: var(--ink); }
  .axis-line { left: 323px; top: 575px; width: 508px; height: 1px; background: #6a6a6a; }
  .axis-label { font-size: 9.5px; font-weight: 700; letter-spacing: 0.5px; }
  .channel-list { list-style: none; font-size: 10px; line-height: 12.5px; font-weight: 600; color: var(--accent-light); }

  .essay { left: 312px; top: 472px; width: 210px; font-size: 8.6px; line-height: 11.8px; }
  .essay__drop { float: left; font-size: 52px; line-height: 40px; font-weight: 200; margin: 2px 6px 0 0; }
  .essay__quote { font-style: italic; color: var(--accent-light); font-size: 10px; line-height: 13px; margin-top: 2px; }
  .essay__credit { text-align: right; font-weight: 700; font-size: 9.5px; margin-top: 2px; padding-right: 8px; }

  .folio { font-size: 8.5px; font-weight: 500; white-space: nowrap; transform-origin: 0 0; }
  .folio--left { left: 24px; top: 745px; transform: rotate(-90deg); }
  .folio--right { left: 566px; top: 662px; transform: rotate(90deg); }
  .folio span.sep { display: inline-block; width: 1px; height: 12px; background: var(--ink); margin: 0 6px; vertical-align: middle; }
  .folio .accent { color: var(--accent-light); }
</style>
</head>
<body>
<div class="spread">
  <section class="page page--left">
    <div class="abs network-art" role="img" aria-label="Decorative network of connected nodes in violet tones"></div>
    <h1 class="abs section-title">Research Questions</h1>
    <p class="abs section-intro">This report is divided into the following six research questions:</p>

    <div class="question" style="left:116px"><div class="question__num">1</div><p class="question__text">How appropriate are private online messaging networks for journalism?</p></div>
    <div class="question" style="left:288px"><div class="question__num">2</div><p class="question__text">Can private messaging be useful for building trust between the journalists and communities?</p></div>
    <div class="question" style="left:466px"><div class="question__num">3</div><p class="question__text">How can journalists use private channels/ platforms to be part of a community?</p></div>

    <h2 class="abs chapter-title">1. The Media Landscape</h2>
    <div class="abs chapter-body">
      <p><strong>If we think about the intersection of the online world and privacy, we can see in the following figure how the last area is the newest and least researched field in journalism, despite its growing influence on issues such as fake news or political communication.</strong></p>
      <p>As it is said, something does not really go completely viral until it arrives in your personal private messaging networks (ChatWave, Wirepost, Direct Messages, text messaging, etc.). That is always a sign. There is a paradox here of private journalism, or journalism transmitted and perhaps even created within private messaging services. How do journalists pay attention to this?</p>
      <p>How could they do it? It would be a kind of journalism based on enabling specific conversations and services to small communities, not just in geographical terms, but communities of interest.</p>
    </div>

    <div class="abs quadrant-label" style="left:323px;top:460px">1. Offline / <b>PUBLIC</b></div>
    <div class="abs headline-word" style="left:370px;top:481px">PUBLIC</div>
    <div class="abs map-note" style="left:370px;top:544px">Traditional mass media</div>
    <div class="abs axis-label" style="left:314px;top:600px;transform:rotate(-90deg);transform-origin:0 0">OFFLINE</div>
    <div class="abs map-note" style="left:370px;top:594px">Offline personal communication on</div>

    <div class="abs folio folio--left">4<span class="sep"></span>The (Private) News Sharing Report</div>
  </section>

  <section class="page page--right">
    <div class="question" style="left:69px"><div class="question__num">4</div><p class="question__text">What are the new skills that the media landscape is requiring of journalists?</p></div>
    <div class="question" style="left:254px"><div class="question__num">5</div><p class="question__text">What do we know about the audience that is using private messaging for News Sharing?</p></div>
    <div class="question" style="left:423px"><div class="question__num">6</div><p class="question__text">What are the best media practices with private online messaging?</p></div>

    <div class="abs headline-word" style="left:19px;top:481px">SIDE</div>
    <div class="abs quadrant-label" style="left:104px;top:460px">2. Online / <b>PUBLIC</b></div>
    <div class="abs map-note" style="left:25px;top:542px">Online media and social media</div>
    <div class="abs axis-label" style="left:280px;top:552px;transform:rotate(90deg);transform-origin:0 0">ONLINE</div>
    <div class="abs map-note" style="left:25px;top:592px">Online private masseging:</div>
    <ul class="abs channel-list" style="left:25px;top:605px">
      <li>ChatWave</li><li>Friendline Messenger</li><li>Text Messaging</li><li>Wirepost</li><li>Direct Messages</li><li>Etc.</li>
    </ul>

    <div class="abs essay">
      <p><span class="essay__drop">W</span>e could define “private journalism” as those processes, products and relationships with the audience made by journalists —in a conscious way- through online private messaging network, most of the time in order to offer more personalized experiences, by building trust and being part of the community of readers itself.</p>
      <p style="text-indent:10px">This journalism is designed to reach a particular profile of audience, those who are using or exploring private communication for news sharing:</p>
      <p class="essay__quote">“I´d say we do [share news on ChatWave] but I think a lot of it would be a news article and then following that, for the next two weeks would be memes and a load of p*ss-takes but depending on the article”</p>
      <p class="essay__credit">—Sam, 18 years old, UK.</p>
    </div>

    <div class="abs folio folio--right">5<span class="sep"></span><span class="accent">Research Questions</span></div>
  </section>

  <div class="abs divider"></div>
  <div class="abs axis-line"></div>
</div>
</body>
</html>
```